Business cards for a fun web development agency

Hi,I am building a web development agency. You can read about it on the website http://kite-loft.examplehost.com. Basically, I want to focus on free and open source products and stay as far away from the corporate business feeling as possible. I want to build a community so I want the business card to feel fun and approachable (at the risk of professional if need be). I am uploading some of my image assets in various file formats. Feel free to use them or make your own if you want just keeping in theme with the website.
Industry/Entity Type
Building
Contact Information for Business Card
Company Name: Boat ShedWebsite: www.kiteloftdev.example (it's currently in alpha on http://kite-loft.examplehost.com if you want to see the them we are trying to capture)My name is: Banner B. SchaferMy email: banner@boatsheddev.comMy phone: 0431 587 904
Look and feel

```html
<!DOCTYPE html>
<html lang="en">
<head>
<meta charset="utf-8">
<title>Kite Loft business cards</title>
<link href="https://fonts.googleapis.com/css2?family=Arimo:wght@400&display=swap" rel="stylesheet">
<style>
  :root {
    --backdrop: #4a413b;
    --card: #151515;
    --card-edge: #202020;
    --ink-white: #f4f4f4;
    --ink-blue: #1c8fcc;
  }
  * { margin: 0; padding: 0; box-sizing: border-box; }
  html, body {
    width: 1200px; height: 780px; overflow: hidden;
    background: var(--backdrop);
    font-family: "Arimo", Arial, sans-serif;
  }
  .canvas { position: relative; width: 1200px; height: 780px; }
  .card {
    position: absolute;
    width: 500px; height: 286px;
    background: var(--card);
    border: 1px solid var(--card-edge);
    border-radius: 3px;
    box-shadow: 0 10px 26px rgba(0,0,0,.45);
  }
  .card-front { left: 70px; top: 90px; }
  .card-back { left: 630px; top: 400px; }

  .wordmark {
    display: flex; align-items: center; gap: 10px;
    font-weight: 400; letter-spacing: 1px; line-height: 1;
  }
  .wordmark .dot {
    width: 34px; height: 34px; border-radius: 50%;
    background: currentColor;
  }
  .card-front .wordmark {
    position: absolute; left: 0; right: 0; top: 118px;
    justify-content: center;
    color: var(--ink-white); font-size: 44px;
  }
  .card-back .wordmark {
    position: absolute; right: 34px; top: 54px;
    color: var(--ink-blue); font-size: 42px;
  }
  .holder {
    position: absolute; left: 34px; top: 180px;
    color: var(--ink-blue); font-size: 21px; letter-spacing: .5px;
  }
  .divider {
    position: absolute; left: 256px; top: 170px;
    width: 2px; height: 76px; background: var(--ink-blue);
  }
  .contacts {
    position: absolute; left: 272px; top: 172px;
    list-style: none; color: var(--ink-blue); font-size: 15px;
  }
  .contacts li { display: flex; align-items: center; gap: 7px; height: 24px; }
  .contacts svg { width: 15px; height: 15px; flex: none; }
</style>
</head>
<body>
<main class="canvas">
  <section class="card card-front">
    <div class="wordmark"><span>KITE</span><span class="dot"></span><span>LOFT</span></div>
  </section>

  <section class="card card-back">
    <div class="wordmark"><span>KITE</span><span class="dot"></span><span>LOFT</span></div>
    <p class="holder">Corwin T. Aldous</p>
    <div class="divider"></div>
    <ul class="contacts">
      <li>
        <svg viewBox="0 0 16 16"><rect width="16" height="16" rx="3" fill="#1c8fcc"/><path d="M5 3.5l2 2-1 1.2c.6 1.3 1.6 2.3 2.9 2.9L10 8.6l2 2-1.3 1.6C7.4 11.8 4.2 8.6 3.8 5.3z" fill="#151515"/></svg>
        <span>0431 587 904</span>
      </li>
      <li>
        <svg viewBox="0 0 16 16"><rect width="16" height="16" rx="3" fill="#1c8fcc"/><circle cx="8" cy="8" r="4.6" fill="none" stroke="#151515" stroke-width="1.2"/><path d="M3.4 8h9.2M8 3.4c-2.2 2.6-2.2 6.6 0 9.2M8 3.4c2.2 2.6 2.2 6.6 0 9.2" fill="none" stroke="#151515" stroke-width="1"/></svg>
        <span>www.kiteloftdev.example</span>
      </li>
      <li>
        <svg viewBox="0 0 16 16"><rect width="16" height="16" rx="3" fill="#1c8fcc"/><rect x="3.2" y="4.6" width="9.6" height="6.8" fill="none" stroke="#151515" stroke-width="1.2"/><path d="M3.2 4.6L8 8.6l4.8-4" fill="none" stroke="#151515" stroke-width="1.2"/></svg>
        <span>corwin@kiteloftdev.example</span>
      </li>
    </ul>
  </section>
</main>
</body>
</html>
```